Hvac and insulation company needs good looking business card design

We are hvac and insulation company and looking for a new business cards that look to today standards designs

Target Market(s)

homeowners

Industry/Entity Type

Hvac

Contact Information for Business Card

Name: Walter Brinoku
Home comfort consultant
address: 4827 Dunmore St #215 Oakland, CA 94619
office: 888-316-2790
cell: 510-742-3185
Lic.# 584261
Email: walter@corvane-hvac.com
Web: corvane-hvac.com

Requirements
Must have
• clean and sleek look
Nice to have
• simple with a clean look
Should not have
• to busy business card

```html
<!DOCTYPE html>
<html lang="en">
<head>
<meta charset="utf-8">
<title>Corvane Home Solutions – Business Card</title>
<link rel="stylesheet" href="https://fonts.googleapis.com/css2?family=Work+Sans:wght@400;500;600&display=swap">
<style>
  :root {
    --orange: #f08322;
    --orange-deep: #c9661a;
    --grey-text: #5d5d5d;
    --grey-line: #8a8a8a;
    --logo-light: #d9d9d9;
    --card-white: #ffffff;
    --backdrop: #e9e9eb;
  }
  * { box-sizing: border-box; margin: 0; padding: 0; }
  html, body { width: 1200px; height: 900px; overflow: hidden; }
  body {
    background: var(--backdrop);
    font-family: "Work Sans", sans-serif;
    display: flex;
    flex-direction: column;
    align-items: center;
    justify-content: center;
    gap: 60px;
  }
  .card {
    position: relative;
    width: 630px;
    height: 360px;
    border-radius: 18px;
    overflow: hidden;
    box-shadow: 0 8px 24px rgba(0,0,0,.18);
  }

  /* Front */
  .card-front { background: linear-gradient(160deg, #f4f4f4 0%, var(--card-white) 55%); }
  .front-wave { position: absolute; inset: 0; width: 100%; height: 100%; }
  .brand { position: absolute; left: 44px; top: 38px; line-height: 1; }
  .brand-name {
    font-weight: 600; font-size: 52px; color: var(--orange); letter-spacing: -1px;
  }
  .brand-tagline {
    font-size: 14px; color: var(--grey-text); letter-spacing: 3px; margin-top: 2px; padding-left: 4px;
  }
  .rule {
    position: absolute; left: 64px; right: 40px; top: 168px;
    height: 1.5px; background: var(--orange);
  }
  .rule-tab {
    position: absolute; right: 0; top: 144px; width: 30px; height: 40px;
    background: var(--orange); border-left: 5px solid var(--grey-line);
  }
  .person { position: absolute; right: 48px; top: 108px; text-align: right; }
  .person-name { color: var(--orange); font-size: 25px; font-weight: 500; letter-spacing: .5px; }
  .person-role { color: var(--grey-text); font-size: 15px; margin-top: 2px; }
  .address {
    position: absolute; right: 48px; top: 186px; text-align: right; font-style: normal;
    color: var(--grey-text); font-size: 15px; line-height: 1.45;
  }
  .contacts {
    position: absolute; left: 36px; top: 182px; list-style: none;
    color: var(--grey-text); font-size: 15px; line-height: 1.5;
  }
  .contacts li { display: flex; align-items: center; gap: 8px; }
  .contacts svg { width: 11px; height: 11px; fill: var(--orange); flex: none; }
  .contacts .web-accent { color: var(--orange); }

  /* Back */
  .card-back {
    background: linear-gradient(135deg, var(--orange) 0%, var(--orange-deep) 100%);
    display: flex; flex-direction: column; align-items: center; justify-content: center;
  }
  .back-brand { text-align: left; line-height: 1; }
  .back-brand .brand-name { color: var(--logo-light); font-size: 92px; }
  .back-brand .brand-tagline { color: var(--logo-light); font-size: 20px; letter-spacing: 5px; }
  .license { color: var(--logo-light); font-size: 20px; letter-spacing: 1px; margin-top: 38px; }
</style>
</head>
<body>

<section class="card card-front" aria-label="Business card front">
  <svg class="front-wave" viewBox="0 0 630 360" preserveAspectRatio="none" aria-hidden="true">
    <path d="M0 292 C 80 326, 190 296, 255 322 C 295 338, 318 350, 332 360 L 0 360 Z" fill="var(--orange)"/>
    <path d="M0 286 C 80 322, 190 290, 258 318 C 298 334, 322 348, 338 360" fill="none" stroke="var(--grey-line)" stroke-width="3"/>
  </svg>

  <div class="brand">
    <div class="brand-name">corvane</div>
    <div class="brand-tagline">home solutions</div>
  </div>

  <div class="person">
    <div class="person-name">WALTER BRINOKU</div>
    <div class="person-role">Home comfort consultant</div>
  </div>
  <div class="rule"></div>
  <div class="rule-tab"></div>

  <ul class="contacts">
    <li><svg viewBox="0 0 24 24"><path d="M6.6 10.8a15 15 0 0 0 6.6 6.6l2.2-2.2a1 1 0 0 1 1-.25 11.4 11.4 0 0 0 3.6.57 1 1 0 0 1 1 1V20a1 1 0 0 1-1 1A17 17 0 0 1 3 4a1 1 0 0 1 1-1h3.5a1 1 0 0 1 1 1c0 1.25.2 2.45.57 3.57a1 1 0 0 1-.25 1z"/></svg><span>888-316-2790</span></li>
    <li><svg viewBox="0 0 24 24"><path d="M7 1h10a2 2 0 0 1 2 2v18a2 2 0 0 1-2 2H7a2 2 0 0 1-2-2V3a2 2 0 0 1 2-2zm0 3v14h10V4z"/></svg><span>510-742-3185</span></li>
    <li><svg viewBox="0 0 24 24"><path d="M2 5h20v14H2zm2 2v.4l8 5 8-5V7z"/></svg><span>walter@corvane-hvac.com</span></li>
    <li><svg viewBox="0 0 24 24"><circle cx="12" cy="12" r="10"/></svg><span>www.<span class="web-accent">corvane-hvac</span>.com</span></li>
  </ul>

  <address class="address">
    4827 Dunmore St<br>#215 Oakland, CA 94619
  </address>
</section>

<section class="card card-back" aria-label="Business card back">
  <div class="back-brand">
    <div class="brand-name">corvane</div>
    <div class="brand-tagline">home solutions</div>
  </div>
  <div class="license">Lic.# 584261</div>
</section>

</body>
</html>
```